Business Card and Letterhead for Pimlu - modern real estate business

I need a double sided business card design for Pimlu. Please see business card brief here https://files.trelvonadocs.com/sheet/r/7QzTmWbaXLJnoPEd-kRyUgFhHsstbvCe2qfoMxDa_pz/view?mode=shared

Please feel free to design the business cards however you feel best. I am happy to give some creative freedoms and then provide feedback from there.

Please then also create a letterhead to match the business card design

Colors

Designer to choose colors to be used in the design.

Requirements
Must have
• Must be a modern, elegant business card which looks very professional

```html
<!DOCTYPE html>
<html lang="en">
<head>
<meta charset="utf-8">
<title>Pimlu Business Card</title>
<link rel="stylesheet" href="https://fonts.googleapis.com/css2?family=Michroma&family=Montserrat:wght@400;500;800&display=swap">
<style>
  :root {
    --page: #e9e7e4;
    --card: #2b2b2d;
    --card-deep: #232325;
    --accent: #e0141c;
    --ink: #ffffff;
    --rule: #8a8a8c;
    --photo-a: #3a3a3d;
    --photo-b: #4b4b4f;
  }
  * { box-sizing: border-box; margin: 0; padding: 0; }
  html, body {
    width: 1200px; height: 800px; overflow: hidden;
    background: var(--page);
    font-family: "Montserrat", Arial, sans-serif;
  }
  .sheet {
    width: 1200px; height: 800px;
    display: flex; align-items: center; justify-content: center; gap: 50px;
  }
  .card {
    width: 540px; height: 309px;
    background: var(--card);
    border: 2px solid var(--accent);
    border-radius: 3px;
    position: relative;
    overflow: hidden;
    box-shadow: 0 10px 24px rgba(0,0,0,0.18);
  }
  /* Front */
  .card--front {
    display: flex; align-items: center; justify-content: center;
  }
  .brand-name {
    font-family: "Montserrat", Arial, sans-serif;
    font-weight: 800;
    font-size: 74px;
    letter-spacing: 6px;
    color: var(--accent);
    text-transform: uppercase;
  }
  /* Back */
  .card--back { display: flex; }
  .portrait {
    width: 225px; height: 100%;
    background: linear-gradient(160deg, var(--photo-b) 0%, var(--photo-a) 60%, var(--card-deep) 100%);
  }
  .details {
    flex: 1;
    display: flex; flex-direction: column; align-items: center;
    padding-top: 52px;
    color: var(--ink);
    text-align: center;
  }
  .agent-name {
    font-family: "Michroma", Arial, sans-serif;
    font-size: 21px;
    color: var(--accent);
    letter-spacing: 1px;
    text-transform: uppercase;
  }
  .agent-role {
    font-size: 14px; font-weight: 500; margin-top: 4px; letter-spacing: 0.3px;
  }
  .icon-rule {
    display: flex; align-items: center; gap: 6px; margin-top: 18px;
  }
  .icon-rule .line { width: 34px; height: 1px; background: var(--rule); }
  .icon {
    width: 17px; height: 17px; border-radius: 50%;
    background: var(--accent);
    display: flex; align-items: center; justify-content: center;
  }
  .contact {
    list-style: none; margin-top: 18px;
    font-size: 14px; font-weight: 500; line-height: 1.35;
  }
  .divider { width: 150px; height: 1px; background: var(--rule); margin: 18px 0 14px; }
  .address { font-size: 14px; font-weight: 500; }
</style>
</head>
<body>
<main class="sheet">
  <section class="card card--front" aria-label="Card front">
    <span class="brand-name">Pimlu</span>
  </section>

  <section class="card card--back" aria-label="Card back">
    <div class="portrait" role="img" aria-label="Portrait photo of the agent in a dark suit"></div>
    <div class="details">
      <h1 class="agent-name">Dane Morrow</h1>
      <p class="agent-role">Licenced Real Estate Agent</p>

      <div class="icon-rule">
        <span class="line"></span>
        <span class="icon">
          <svg width="10" height="10" viewBox="0 0 24 24"><path fill="#fff" d="M6.6 10.8a15.1 15.1 0 0 0 6.6 6.6l2.2-2.2c.3-.3.7-.4 1-.2 1.1.4 2.3.6 3.6.6.6 0 1 .4 1 1V20c0 .6-.4 1-1 1A17 17 0 0 1 3 4c0-.6.4-1 1-1h3.5c.6 0 1 .4 1 1 0 1.3.2 2.5.6 3.6.1.3 0 .7-.2 1z"/></svg>
        </span>
        <span class="icon">
          <svg width="10" height="10" viewBox="0 0 24 24"><rect x="2" y="5" width="20" height="14" rx="1.5" fill="#fff"/><path d="M2.5 6l9.5 7 9.5-7" fill="none" stroke="#e0141c" stroke-width="2"/></svg>
        </span>
        <span class="icon">
          <svg width="10" height="10" viewBox="0 0 24 24" fill="none" stroke="#fff" stroke-width="2.2"><circle cx="12" cy="12" r="9"/><ellipse cx="12" cy="12" rx="4" ry="9"/><path d="M3 12h18"/></svg>
        </span>
        <span class="line"></span>
      </div>

      <ul class="contact">
        <li>0400 318 592</li>
        <li>dane@pimlu.com</li>
        <li>www.pimlu.com</li>
      </ul>
      <div class="divider"></div>
      <p class="address">PO Box 1190, Fernvale Ridge NSW 2791</p>
    </div>
  </section>
</main>
</body>
</html>
```